Lanternfield Drinks business cards

We need a business card design for our new logo. The company is modern, progressive, professional, yet approachable. The key products are ready to drink bottles and cans of coffee based beverages.
These cards will be a critical part of the first impression made by our sales organization, business development team, and all external facing personnel.
Card can be a vertical or horizontal orientation.

Target Market(s)

Customers, suppliers, business partners

Industry/Entity Type

Business

Contact Information for Business Card

Business cards should feature Company Name and Logo.

Font styles to use
Serif

Colors

Designer to choose colors to be used in the design.

Requirements
Must have
• Strong readability of Name, phone #, mobile number and email address.
• Job title, website url, Street Address, and other details can be secondary level readability.
Nice to have
• High impact, simplistic quality design.
• Ok to utilize the 'H in the box' separate from the company name

```html
<!DOCTYPE html>
<html lang="en">
<head>
<meta charset="utf-8">
<title>Lanternfield Drinks business cards</title>
<link href="https://fonts.googleapis.com/css2?family=Noto+Serif:wght@400;700&family=Montserrat:wght@400&display=swap" rel="stylesheet">
<style>
  :root {
    --backdrop: #151515;
    --orange-deep: #e8612f;
    --orange-light: #f49a52;
    --gold: #d9ab45;
    --paper: #f4f4f4;
    --paper-shade: #e2e2e2;
    --ink: #3a3a3a;
    --charcoal: #2a292a;
    --charcoal-light: #3a393a;
    --white: #ffffff;
  }
  * { box-sizing: border-box; margin: 0; padding: 0; }
  html, body { width: 1200px; height: 864px; overflow: hidden; }
  body {
    background: var(--backdrop);
    font-family: "Noto Serif", Georgia, serif;
    position: relative;
  }
  .card {
    position: absolute;
    top: 289px;
    width: 500px;
    height: 286px;
    border-radius: 3px;
    overflow: hidden;
    box-shadow: 0 12px 30px rgba(0,0,0,.6);
  }
  .card--front { left: 80px; background: linear-gradient(180deg, var(--paper), var(--paper-shade)); }
  .card--back { left: 620px; background: var(--charcoal); }

  /* front */
  .brand-band {
    height: 122px;
    background: linear-gradient(90deg, var(--orange-deep), var(--orange-light));
    display: flex;
    align-items: center;
    padding-left: 30px;
    gap: 16px;
  }
  .brand-mark {
    width: 60px; height: 60px;
    border: 4px solid var(--white);
    flex: none;
  }
  .brand-name {
    font-weight: 700;
    font-size: 27px;
    letter-spacing: .5px;
    color: var(--white);
    text-transform: uppercase;
  }
  .contact {
    position: absolute;
    left: 30px; top: 142px;
    font-size: 12px;
    color: var(--ink);
    line-height: 1.35;
  }
  .contact__address { margin-bottom: 8px; }
  .contact__list { list-style: none; }
  .contact__list li { display: flex; align-items: center; gap: 9px; margin-bottom: 3px; }
  .contact__list svg { width: 11px; height: 11px; flex: none; }
  .person {
    position: absolute;
    right: 28px; bottom: 26px;
    width: 150px;
    text-align: center;
  }
  .person__name {
    font-size: 12px;
    font-weight: 700;
    letter-spacing: .6px;
    color: var(--orange-deep);
    text-transform: uppercase;
    margin-bottom: 8px;
  }
  .person__title {
    background: var(--gold);
    color: var(--white);
    font-family: "Montserrat", Arial, sans-serif;
    font-size: 11px;
    padding: 11px 0;
  }

  /* back */
  .pattern-field {
    position: absolute; inset: 0;
    background: linear-gradient(135deg, var(--charcoal-light), var(--charcoal));
  }
  .back-brand {
    position: absolute;
    inset: 0;
    display: flex;
    align-items: center;
    justify-content: center;
    gap: 16px;
  }
  .back-brand .brand-mark { border-color: var(--orange-deep); }
  .back-brand .brand-name { color: var(--orange-deep); }
</style>
</head>
<body>
  <section class="card card--front">
    <header class="brand-band">
      <div class="brand-mark"></div>
      <div class="brand-name">Lanternfield Drinks Co.</div>
    </header>

    <div class="contact">
      <p class="contact__address">418 Harbor Lane<br>Millbrook, NY 12545</p>
      <ul class="contact__list">
        <li><svg viewBox="0 0 12 12"><rect x=".5" y=".5" width="11" height="11" fill="none" stroke="#e8612f"/><path d="M3.5 3c0 3 2.5 5.5 5.5 5.5l.4-1.3-1.6-.8-.6.7C6 6.6 5.4 6 5 5.2l.7-.6-.8-1.6z" fill="#e8612f"/></svg>555.014.2290</li>
        <li><svg viewBox="0 0 12 12"><rect x=".5" y=".5" width="11" height="11" fill="none" stroke="#e8612f"/><rect x="4" y="2.5" width="4" height="7" rx=".6" fill="none" stroke="#e8612f"/></svg>555.016.7734</li>
        <li><svg viewBox="0 0 12 12"><rect x=".5" y=".5" width="11" height="11" fill="#e8612f"/><rect x="2.5" y="3.5" width="7" height="5" fill="none" stroke="#fff"/><path d="M2.5 3.5 6 6.3l3.5-2.8" fill="none" stroke="#fff"/></svg>daniel@lanternfielddrinks.com</li>
        <li><svg viewBox="0 0 12 12"><rect x=".5" y=".5" width="11" height="11" fill="#e8612f"/><circle cx="6" cy="6" r="3.3" fill="none" stroke="#fff"/><path d="M2.7 6h6.6M6 2.7v6.6" stroke="#fff"/></svg>www.lanternfielddrinks.com</li>
      </ul>
    </div>

    <div class="person">
      <p class="person__name">Daniel Ashcombe</p>
      <p class="person__title">Managing Director</p>
    </div>
  </section>

  <section class="card card--back">
    <div class="pattern-field" role="img" aria-label="Faint repeating tile pattern of the company monogram on charcoal"></div>
    <div class="back-brand">
      <div class="brand-mark"></div>
      <div class="brand-name">Lanternfield Drinks Co.</div>
    </div>
  </section>
</body>
</html>
```